Website for Excavator and Earthworks Company

We require a modern, sleek and practical website for our newly created earthworks/excavator business in Perth, Western Australia called Bluegum Ridge Earthworks.

The website should have a modern, cutting edge feel but only needs to be relatively simplistic in it's layout and eventual functionality.

Some pages it should have would be Home, About, Projects and Contact Us.

```html
<!DOCTYPE html>
<html lang="en">
<head>
<meta charset="utf-8">
<title>Bluegum Ridge Earthworks</title>
<link href="https://fonts.googleapis.com/css2?family=Montserrat:wght@700;800&family=Poppins:wght@400;500;600;700&family=Syncopate:wght@700&display=swap" rel="stylesheet">
<style>
:root{
  --lime:#c9da00;
  --navy:#101d45;
  --ink:#1b1b1b;
  --text:#333;
  --muted:#666;
  --light:#f2f2f2;
  --footer:#1c1c1c;
  --white:#fff;
}
*{box-sizing:border-box;margin:0;padding:0}
html,body{width:1200px;height:4170px;overflow:hidden}
body{font-family:"Poppins",sans-serif;color:var(--text);background:var(--white);position:relative}
.abs{position:absolute}
.btn{position:absolute;display:flex;align-items:center;justify-content:center;font:600 12px "Poppins",sans-serif;text-transform:uppercase;color:var(--ink)}
.btn-lime{background:var(--lime)}
.btn-white{background:var(--white)}
.section-title{position:absolute;left:0;width:1200px;text-align:center;font:700 27px "Syncopate",sans-serif;color:var(--navy);letter-spacing:-1px}
.rule{position:absolute;height:2px;background:var(--lime)}
.rule-c{left:555px;width:90px}
.rule-c::after{content:"";position:absolute;left:37px;top:-6px;width:14px;height:14px;background:var(--lime);border-radius:50%}

/* header */
.topbar{left:355px;top:0;width:845px;height:36px;background:var(--lime);clip-path:polygon(22px 0,100% 0,100% 100%,0 100%)}
.topbar .info{position:absolute;top:9px;font-size:12px;color:var(--ink);display:flex;align-items:center;gap:10px}
.topbar .ic{width:22px;height:22px;border-radius:50%;background:var(--white);display:flex;align-items:center;justify-content:center}
.topbar .quote{position:absolute;left:520px;top:0;width:185px;height:36px;background:#111;color:var(--white);font:600 13px "Poppins",sans-serif;display:flex;align-items:center;justify-content:center;clip-path:polygon(10px 0,100% 0,100% 100%,0 100%)}
.brand{left:140px;top:50px;font:700 20px "Poppins",sans-serif;color:var(--ink);display:flex;align-items:center;gap:10px}
.brand .sq{width:26px;height:26px;background:var(--lime)}
.nav{top:68px;left:676px;display:flex;gap:34px;font:500 13px "Poppins",sans-serif;letter-spacing:1px;color:var(--ink)}

/* hero */
.hero{left:0;top:108px;width:1200px;height:565px;background:linear-gradient(100deg,#2b2420 0%,#6a3a1c 35%,#c2622a 55%,#8a4a22 75%,#3a2a1e 100%)}
.hero-title{left:141px;top:240px;font:800 50px/58px "Montserrat",sans-serif;color:var(--white);text-transform:uppercase}
.hero-title span{font-weight:400;display:block}
.hero-sub{left:141px;top:418px;width:380px;font-size:12px;line-height:18px;color:var(--white)}

/* about */
.about-img{left:0;top:770px;width:610px;height:345px;background:linear-gradient(135deg,#9a8a70,#6d6a5e 50%,#b39a6f)}
.about-eyebrow{left:657px;top:735px;font-size:12px;color:var(--ink)}
.about-title{left:657px;top:752px;font:700 27px/36px "Syncopate",sans-serif;color:var(--navy);letter-spacing:-1px}
.about-text{left:657px;top:862px;width:405px;font-size:12.5px;line-height:22.5px;color:var(--ink)}
.about-text p+p{margin-top:8px}

/* services */
.card{position:absolute;top:1288px;width:273px;height:389px;color:var(--white)}
.card .ph{position:absolute;inset:0}
.card .shade{position:absolute;inset:0;background:linear-gradient(transparent 50%,rgba(0,0,0,.75))}
.card h3{position:absolute;left:0;right:0;top:282px;text-align:center;font:700 18px "Montserrat",sans-serif;text-transform:uppercase}
.card p{position:absolute;left:25px;right:25px;top:312px;text-align:center;font-size:12px;line-height:20px}
.arrow{position:absolute;top:1712px;width:36px;height:36px;border-radius:50%;display:flex;align-items:center;justify-content:center}

/* projects */
.proj{position:absolute}
.proj-label{position:absolute;text-align:center;font:500 12.5px/18px "Poppins",sans-serif;color:var(--ink)}

/* why */
.why-item{position:absolute;font-size:12.5px;line-height:18px;color:#444}
.why-item h4{font:500 14px "Poppins",sans-serif;color:var(--ink);margin-bottom:2px}
.why-ic{position:absolute;width:58px;height:58px;border-radius:50%;background:var(--white);box-shadow:0 3px 10px rgba(0,0,0,.15);display:flex;align-items:center;justify-content:center}

/* contact */
.contact{left:0;top:3163px;width:1200px;height:610px;background:var(--light)}
.field{position:absolute;background:var(--white);border:1px solid #ddd;font-size:11px;color:#888;padding:18px 14px}

/* footer */
.footer{left:0;top:3773px;width:1200px;height:397px;background:var(--footer);color:var(--white)}
.fcol h5{font:500 17px "Poppins",sans-serif;margin-bottom:10px;text-transform:uppercase}
.fcol{position:absolute;font-size:13px;line-height:26px}
.soc{display:flex;align-items:center;gap:10px;margin-bottom:11px;font-size:13px}
.soc i{width:30px;height:30px;border-radius:50%;border:1px solid var(--white);display:block}
.soc i.on{background:var(--lime);border-color:var(--lime)}
</style>
</head>
<body>

<!-- header -->
<div class="abs topbar">
  <div class="info" style="left:30px"><span class="ic"><svg width="12" height="12" viewBox="0 0 24 24"><path d="M6.6 10.8a15 15 0 0 0 6.6 6.6l2.2-2.2c.3-.3.7-.4 1-.2 1.1.4 2.3.6 3.6.6.6 0 1 .4 1 1V20c0 .6-.4 1-1 1A17 17 0 0 1 3 4c0-.6.4-1 1-1h3.5c.6 0 1 .4 1 1 0 1.3.2 2.5.6 3.6.1.3 0 .7-.2 1z" fill="#111"/></svg></span>Phone: <b>(08) 9000 1122</b></div>
  <div class="info" style="left:230px"><span class="ic"><svg width="12" height="12" viewBox="0 0 24 24"><path d="M2 5h20v14H2z" fill="#111"/><path d="M2 5l10 8 10-8" stroke="#fff" stroke-width="1.5" fill="none"/></svg></span>Email: <b>info@bluegumridge.com.au</b></div>
  <div class="quote">GET A QUOTE TODAY</div>
</div>
<div class="abs brand"><span class="sq"></span>Bluegum Ridge</div>
<nav class="abs nav"><span>HOME</span><span>ABOUT</span><span>PROJECTS</span><span>CONTACT US</span></nav>

<!-- hero -->
<div class="abs hero" role="img" aria-label="Excavator digging on a site under an orange sunset sky"></div>
<h1 class="abs hero-title">Earth Moving<br>Excellence<span>In Perth</span></h1>
<p class="abs hero-sub">Professional Excavation, Bulk Earthworks, Site Preparation And Land Development Services Across Perth And Western Australia.</p>
<div class="btn btn-lime" style="left:141px;top:495px;width:156px;height:45px">Get A Quote Today</div>
<div class="btn btn-white" style="left:310px;top:495px;width:160px;height:45px">View Our Projects</div>

<!-- about -->
<div class="abs about-img" role="img" aria-label="Site workers in hi-vis vests with excavators on an earthworks site"></div>
<div class="abs about-eyebrow">ABOUT US</div>
<h2 class="abs about-title">Bluegum Ridge<br>Earth Works</h2>
<div class="rule" style="left:659px;top:843px;width:70px"></div>
<div class="abs about-text">
  <p>Bluegum Ridge Earthworks is Perth's trusted partner for excavation and earthmoving solutions. Founded on principles of precision, reliability, and uncompromising quality, we've built our reputation one project at a time.</p>
  <p>Our team brings decades of combined experience to every job, from residential site preparation to large-scale commercial developments. We invest in the latest equipment and technology to ensure efficiency, safety, and superior results.</p>
</div>
<div class="btn btn-lime" style="left:658px;top:1076px;width:124px;height:45px">Work With Us</div>

<!-- services -->
<h2 class="section-title" style="top:1195px">Our Services</h2>
<div class="rule rule-c" style="top:1252px"></div>
<div class="card" style="left:27px"><div class="ph" role="img" aria-label="Excavator at a residential house site" style="background:linear-gradient(#8ea0b0,#7a6a55 55%,#5a4a38)"></div><div class="shade"></div><h3>Site Excavation</h3><p>Professional Site Preparation And Excavation Services For Residential And Commercial Developments.</p></div>
<div class="card" style="left:317px"><div class="ph" role="img" aria-label="Loader clearing vegetation on sandy land" style="background:linear-gradient(#a78a66,#8a6d4c 55%,#5c4631)"></div><div class="shade"></div><h3>Land Clearing</h3><p>Efficient Land Clearing And Vegetation Removal To Prepare Your Site For Construction.</p></div>
<div class="card" style="left:606px"><div class="ph" role="img" aria-label="Workers installing drainage in a trench" style="background:linear-gradient(#9aa6a0,#8a7156 45%,#5a4533)"></div><div class="shade"></div><h3>Drainage Solutions</h3><p>Expert Trenching And Drainage Installation To Manage Water Flow And Prevent Erosion.</p></div>
<div class="card" style="left:895px"><div class="ph" role="img" aria-label="Dozers shaping a large earthworks cut" style="background:linear-gradient(#a9c4d6,#b08a5e 35%,#7a5a3c)"></div><div class="shade"></div><h3>Bulk Earthworks</h3><p>Large-Scale Earthmoving Projects Including Cut And Fill, Embankments, And Leveling.</p></div>
<div class="arrow" style="left:556px;border:1px solid #333"><svg width="14" height="14" viewBox="0 0 24 24"><path d="M20 12H5M11 6l-6 6 6 6" stroke="#333" stroke-width="2" fill="none"/></svg></div>
<div class="arrow" style="left:607px;background:var(--lime)"><svg width="14" height="14" viewBox="0 0 24 24"><path d="M4 12h15M13 6l6 6-6 6" stroke="#111" stroke-width="2" fill="none"/></svg></div>

<!-- projects -->
<h2 class="section-title" style="top:1826px">Featured Projects</h2>
<div class="rule rule-c" style="top:1882px"></div>
<p class="abs" style="left:0;width:1200px;top:1898px;text-align:center;font-size:12.5px;color:var(--ink)">Explore our portfolio of completed earthworks projects across Perth and Western Australia.</p>
<div class="proj" style="left:143px;top:1982px;width:395px;height:394px" role="img" aria-label="Excavator preparing a large flat commercial site"><div style="position:absolute;inset:0;background:linear-gradient(#9aa8b4,#8a7a62 45%,#4e4030)"></div><div style="position:absolute;inset:0;background:linear-gradient(transparent 60%,rgba(0,0,0,.7))"></div>
  <div style="position:absolute;left:19px;top:302px;color:#fff"><div style="font:600 10px Poppins,sans-serif">COMMERCIAL</div><div style="font:600 20px Poppins,sans-serif">Joondalup Business Park</div><div style="font-size:12px;line-height:15px;width:290px">Large-scale site preparation for 12-hectare commercial development</div></div>
  <svg class="abs" style="left:346px;top:342px" width="30" height="12" viewBox="0 0 30 12"><path d="M0 6h28M22 1l6 5-6 5" stroke="var(--lime)" stroke-width="2" fill="none"/></svg></div>
<div class="proj" style="left:551px;top:1953px;width:161px;height:397px;background:linear-gradient(#a8bccc,#9a8466 35%,#c9a679)" role="img" aria-label="Aerial view of a residential subdivision under construction"></div>
<div class="proj-label" style="left:551px;top:2356px;width:161px">Scarborough<br>Subdivision</div>
<div class="proj" style="left:724px;top:1982px;width:163px;height:397px;background:linear-gradient(#b4b6b0,#8a7454 50%,#5e4a34)" role="img" aria-label="Excavator bucket on a road works site"></div>
<div class="proj-label" style="left:724px;top:2390px;width:163px">Fremantle<br>Road Works</div>
<div class="proj" style="left:898px;top:1953px;width:163px;height:397px;background:linear-gradient(#8c95a0,#6e7078 35%,#7a5c40)" role="img" aria-label="Excavator beside a warehouse building"></div>
<div class="proj-label" style="left:898px;top:2360px;width:163px">Welshpool<br>Warehouse</div>

<!-- why choose us -->
<h2 class="section-title" style="top:2503px">Why Choose Us</h2>
<div class="rule rule-c" style="top:2560px"></div>
<svg class="abs" style="left:410px;top:2600px" width="380" height="380"><circle cx="190" cy="190" r="185" fill="none" stroke="#bbb" stroke-dasharray="4 4"/></svg>
<div class="abs" style="left:455px;top:2643px;width:290px;height:290px;border-radius:50%;background:radial-gradient(circle,#8a8478,#5c5a56 60%,#3f5a7a)" role="img" aria-label="Excavator on a rocky site"></div>
<div class="abs" style="left:455px;top:2790px;width:290px;text-align:center;font:600 20px Poppins,sans-serif;color:#fff">Bluegum Ridge</div>
<div class="why-ic" style="left:415px;top:2608px"><svg width="28" height="28" viewBox="0 0 24 24"><path d="M6 2h9l4 4v16H6z" fill="#111"/><path d="M9 9h7M9 12h7M9 15h5" stroke="#fff"/></svg></div>
<div class="why-item" style="left:200px;top:2630px;width:195px;text-align:right"><h4>Licensed &amp; Insured</h4>Fully Compliant With WA Regulations</div>
<div class="why-ic" style="left:735px;top:2608px"><svg width="28" height="28" viewBox="0 0 24 24"><path d="M12 2a5 5 0 0 1 5 5c0 4-5 9-5 9s-5-5-5-9a5 5 0 0 1 5-5z" fill="#111"/><path d="M3 20h18" stroke="#111" stroke-width="2"/></svg></div>
<div class="why-item" style="left:817px;top:2627px;width:190px"><h4>Site-Specific Solutions</h4>Tailored Approaches For Perth's Unique Terrain.</div>
<div class="why-ic" style="left:367px;top:2775px"><svg width="30" height="30" viewBox="0 0 24 24"><circle cx="12" cy="12" r="9" fill="none" stroke="#111" stroke-width="2"/><path d="M12 7v5l3 3" stroke="#111" stroke-width="2" fill="none"/></svg></div>
<div class="why-item" style="left:180px;top:2778px;width:162px;text-align:right"><h4>On-Time Delivery</h4>We Respect Your Schedule</div>
<div class="why-ic" style="left:775px;top:2775px"><svg width="30" height="30" viewBox="0 0 24 24"><circle cx="8" cy="9" r="3" fill="#111"/><circle cx="16" cy="9" r="3" fill="#111"/><path d="M2 20c0-4 3-6 6-6s6 2 6 6zM10 20c0-4 3-6 6-6s6 2 6 6z" fill="#111"/></svg></div>
<div class="why-item" style="left:857px;top:2778px;width:170px"><h4>Clear Communication</h4>We Keep You Informed At Every Step.</div>
<div class="why-ic" style="left:425px;top:2905px"><svg width="30" height="30" viewBox="0 0 24 24"><circle cx="12" cy="6" r="3" fill="#111"/><circle cx="5" cy="10" r="2.5" fill="#111"/><circle cx="19" cy="10" r="2.5" fill="#111"/><path d="M6 21c0-5 3-8 6-8s6 3 6 8zM1 19c0-3 2-5 4-5M23 19c0-3-2-5-4-5" fill="#111" stroke="#111"/></svg></div>
<div class="why-item" style="left:240px;top:2920px;width:160px;text-align:right"><h4>Expert Team</h4>Skilled Operators On Every Job</div>
<div class="why-ic" style="left:712px;top:2905px"><svg width="30" height="30" viewBox="0 0 24 24"><path d="M1 10l5-4 6 5 6-5 5 4-9 8z" fill="#111"/></svg></div>
<div class="why-item" style="left:795px;top:2928px;width:160px"><h4>20 Years Of Experience</h4>Lorem Ipsum Is Simply Dummy Text</div>
<div class="btn btn-lime" style="left:520px;top:3030px;width:159px;height:45px">Get A Quote Today</div>

<!-- contact -->
<div class="abs contact"></div>
<h2 class="section-title" style="top:3240px">Get In Touch</h2>
<div class="rule rule-c" style="top:3296px"></div>
<p class="abs" style="left:370px;width:460px;top:3310px;text-align:center;font-size:12.5px;line-height:18px;color:var(--ink)">Ready To Move Earth? Contact Our Perth Team For A No-Obligation Site Assessment And Quote.</p>
<div class="field" style="left:292px;top:3370px;width:300px;height:52px">First Name</div>
<div class="field" style="left:607px;top:3370px;width:300px;height:52px">Last Name</div>
<div class="field" style="left:292px;top:3438px;width:300px;height:52px">Your Email</div>
<div class="field" style="left:607px;top:3438px;width:300px;height:52px">Phone</div>
<div class="field" style="left:292px;top:3506px;width:615px;height:107px">Your Message</div>
<div class="btn btn-lime" style="left:292px;top:3635px;width:615px;height:53px">Submit Now</div>

<!-- footer -->
<div class="abs footer"></div>
<div class="abs" style="left:141px;top:3895px;display:flex;align-items:center;gap:10px;font:700 20px Poppins,sans-serif;color:#fff"><span style="width:26px;height:26px;background:var(--lime)"></span>Bluegum Ridge</div>
<p class="abs" style="left:141px;top:3940px;width:270px;font-size:12.5px;line-height:20px;color:#fff">Lorem Ipsum Is Simply Dummy Text Of The Printing And Typesetting Industry.</p>
<div class="abs" style="left:141px;top:3998px;width:262px;height:36px;border-radius:18px;background:#fff;font-size:11px;color:#999;padding:10px 32px">Your Email</div>
<div class="abs" style="left:370px;top:4004px;width:25px;height:25px;border-radius:50%;background:var(--lime);display:flex;align-items:center;justify-content:center"><svg width="12" height="12" viewBox="0 0 24 24"><path d="M4 12h15M13 6l6 6-6 6" stroke="#111" stroke-width="2.5" fill="none"/></svg></div>
<div class="fcol" style="left:504px;top:3855px"><h5>Quick Links</h5>Home<br>About<br>Projects<br>Contact Us</div>
<div class="fcol" style="left:692px;top:3855px;width:200px;line-height:19px"><h5 style="margin-bottom:14px">Contact Details</h5>
  <div style="padding-left:22px;position:relative;margin-bottom:12px"><svg class="abs" style="left:0;top:2px" width="12" height="14" viewBox="0 0 24 28"><path d="M12 0a10 10 0 0 1 10 10c0 8-10 18-10 18S2 18 2 10A10 10 0 0 1 12 0z" fill="#fff"/></svg>Perth, Western Australia</div>
  <div style="padding-left:22px;position:relative;margin-bottom:12px"><svg class="abs" style="left:0;top:2px" width="12" height="12" viewBox="0 0 24 24"><path d="M6.6 10.8a15 15 0 0 0 6.6 6.6l2.2-2.2c.3-.3.7-.4 1-.2 1.1.4 2.3.6 3.6.6.6 0 1 .4 1 1V20c0 .6-.4 1-1 1A17 17 0 0 1 3 4c0-.6.4-1 1-1h3.5c.6 0 1 .4 1 1 0 1.3.2 2.5.6 3.6.1.3 0 .7-.2 1z" fill="#fff"/></svg>Phone<br>+61 400 555 019</div>
  <div style="padding-left:22px;position:relative"><svg class="abs" style="left:0;top:4px" width="12" height="10" viewBox="0 0 24 18"><path d="M0 0h24v18H0z" fill="#fff"/></svg>Email<br>info@bluegumridge.com.au</div></div>
<div class="fcol" style="left:948px;top:3855px"><h5 style="margin-bottom:12px">Social Media</h5>
  <div class="soc"><i class="on"></i>Community</div><div class="soc"><i></i>Video Channel</div><div class="soc"><i></i>Careers</div><div class="soc"><i></i>Photo Gallery</div></div>
<div class="abs" style="left:141px;top:4117px;width:918px;height:1px;background:#444"></div>
<p class="abs" style="left:0;width:1200px;top:4135px;text-align:center;font-size:12px;color:#fff">© 2026 Bluegum Ridge Earthworks. All Rights Reserved. | ABN: 98 765 432 109</p>

</body>
</html>
```